Modernize and improve usability of our webpage www.lernwandel.ch (4 languages, mostly static content)

Need to modernize and freshen up the webpages of our association: www.lernwandel.ch We offer apprenticeship exchanges within Switzerland and abroad. Young people can inform and enroll online. We do the matchmaking with work locations and organize logistics, stay overs etc.
The webpage needs to be in 4 languages (German, French, Italian and English). The main pages will be:
- Landing page: what we do, targeted to our apprentices / young people who enroll for the stages.
- Sup-Page: Registration form for interested apprentices to sign up for the program
- Sub-Page "Company", the firms who would like to send their apprentices on a internship and info on how to join the program
- Sub-Page "Host Family", private people who would be interested in hosting the apprentices (for free) during the stages. Find out about the reqiurements for the host families
- Sub-Page "About Us", who we are, executive team, board of director, our sponsor "Falkner Circle Switzerland"
- Footer: contact (E-Mail, Telephone, WhatsApp), Bank details (IBAN Number), Partnerlogo of Falkner-Circle (see uploaded jpg), Social-Media Links (Facebook, LinkedIn)

Target Market(s)

Young people looking for a "apprenticeship" stage within Switzerland or going from Switzerland abroad

Industry/Entity Type

Apprenticeships: cooks, builders, craftsman, office support, etc.

Number of Pages Required

5+ page

Font styles to use
Other font styles liked:
• Lato (sans serif)

Requirements
Must have
• use colors shown on uploaded PDF-Slides: Make the BLUE the MAIN color, the ORANGE as a secondary color
Nice to have
• Forms using e.g. google forms or survey-monkey forms (external links, no code). Matching & appealing visuals showing young apprentices (can use stock photos)

```html
<!DOCTYPE html>
<html lang="en">
<head>
<meta charset="utf-8">
<title>Lernwandel – Apprentices Exchange</title>
<link href="https://fonts.googleapis.com/css2?family=Lato:wght@400;700;900&family=Ubuntu:wght@500;700&display=swap" rel="stylesheet">
<style>
:root{
  --navy:#0c1a47;
  --navy-deep:#0a1638;
  --ink:#1b2163;
  --orange:#ff7a00;
  --grey-bg:#f3f4f6;
  --text:#7d7f8a;
  --white:#ffffff;
}
*{box-sizing:border-box;margin:0;padding:0}
html,body{width:1200px;height:4177px;overflow:hidden;background:var(--white)}
body{font-family:"Lato",sans-serif;color:var(--text);position:relative}
.abs{position:absolute}
.heading{font-family:"Ubuntu",sans-serif;font-weight:500;color:var(--ink)}
.eyebrow{font-family:"Lato",sans-serif;font-weight:700;color:var(--orange);font-size:16px}
.btn-orange{background:var(--orange);color:var(--white);font-weight:700;font-size:16px;display:flex;align-items:center;justify-content:center;gap:12px;border-radius:3px}
section{position:absolute;left:0;width:1200px;overflow:hidden}

/* header */
.site-header{top:0;height:101px;background:var(--white);border-bottom:1px solid #e4e6ec}
.topbar{left:381px;top:0;width:819px;height:33px;background:var(--navy);clip-path:polygon(0 0,100% 0,100% 100%,22px 100%)}
.topbar-item{top:0;height:33px;display:flex;align-items:center;gap:8px;color:var(--white);font-size:11px;font-weight:700}
.topbar-cta{left:213px;width:233px;background:var(--orange);justify-content:center}
.brand{left:165px;top:30px;font-family:"Ubuntu",sans-serif;font-weight:500;font-size:34px;color:var(--orange);line-height:1}
.nav a{position:absolute;top:61px;font-size:11px;color:#4a4d5c;text-decoration:none}
.nav a.active{font-weight:700;color:var(--ink)}
.header-cta{left:933px;top:54px;width:117px;height:29px;border:1.5px solid var(--ink);border-radius:3px;font-size:11px;font-weight:700;color:var(--ink);display:flex;align-items:center;justify-content:center}

/* hero */
.hero{top:101px;height:616px}
.hero-photo{inset:0;background:radial-gradient(ellipse at 60% 20%,#b89a86 0%,#5c5253 30%,#2a2f45 65%,#1a1f33 100%)}
.hero-shade{inset:0;background:rgba(12,20,55,.55)}
.hero-badge{left:517px;top:199px;width:164px;height:37px;background:var(--navy);border-radius:3px;color:var(--white);font-size:12px;font-weight:900;display:flex;align-items:center;justify-content:center;letter-spacing:.3px}
.hero-title{left:0;top:247px;width:1200px;text-align:center;font-family:"Ubuntu",sans-serif;font-weight:500;font-size:65px;line-height:72px;color:var(--white)}
.hero-btn{left:517px;top:418px;width:164px;height:46px;border:1.5px solid var(--white);border-radius:3px;color:var(--white);font-size:12px;font-weight:900;display:flex;align-items:center;justify-content:center}

/* about */
.about{top:717px;height:642px;background:var(--white)}
.mosaic{left:77px;top:76px}
.about-eyebrow{left:639px;top:113px}
.about-title{left:639px;top:144px;font-size:45px;line-height:56px;width:520px}
.about-text{left:639px;top:262px;width:460px;font-size:14.5px;line-height:24px}
.about-btn{left:641px;top:501px;width:154px;height:44px}

/* services */
.services{top:1359px;height:672px;background:var(--navy-deep)}
.services-eyebrow{left:0;width:1200px;text-align:center;top:105px}
.services-title{left:0;width:1200px;text-align:center;top:134px;font-size:48px;color:var(--white)}
.service-card{top:248px;width:320px;height:340px}
.service-photo{left:0;top:52px;width:100%;height:242px}
.service-ring{left:108px;top:-4px;width:104px;height:104px;border-radius:50%;border:1.5px solid rgba(255,255,255,.55);clip-path:inset(0 0 50% 0)}
.service-icon{left:120px;top:8px;width:80px;height:80px;border-radius:50%;background:var(--orange);display:flex;align-items:center;justify-content:center}
.service-label{left:15px;top:260px;width:287px;height:79px;background:var(--white);border-radius:4px;text-align:center;padding-top:13px}
.service-label h3{font-family:"Ubuntu",sans-serif;font-weight:500;font-size:18px;color:var(--ink)}
.service-label p{font-size:12.5px;margin-top:8px;color:var(--text)}

/* projects */
.projects{top:2031px;height:592px;background:var(--grey-bg)}
.projects-title{left:105px;top:89px;font-size:36px;line-height:42px}
.tab{top:204px;height:44px;border-radius:3px;font-size:16px;display:flex;align-items:center;justify-content:center;background:var(--white);color:#6b6e7c;box-shadow:0 2px 6px rgba(0,0,0,.08)}
.tab.active{background:var(--orange);color:var(--white);font-weight:700}
.projects-photo{left:107px;top:292px;width:222px;height:228px;background:linear-gradient(135deg,#d8cdb8,#b7a77a 45%,#8a7450);border-radius:2px}
.projects-text{left:368px;top:288px;width:330px;font-size:14px;line-height:24px}
.check{left:368px;display:flex;align-items:center;gap:12px;font-size:14px}
.projects-people{left:783px;top:45px;width:417px;height:547px;background:linear-gradient(160deg,#e2e4ea 0%,#b4bccb 40%,#3c4257 100%);clip-path:polygon(18% 12%,55% 0,100% 0,100% 100%,0 100%,4% 45%)}

/* enroll */
.enroll{top:2623px;height:436px}
.enroll-bg{inset:0;background:linear-gradient(90deg,#27345f,#1f2b55 50%,#2a365c)}
.enroll-shade{inset:0;background:rgba(12,22,62,.72)}
.enroll-title{left:109px;top:144px;font-size:45px;line-height:57px;color:var(--white)}
.enroll-form-title{left:693px;width:392px;top:85px;text-align:center;font-family:"Ubuntu",sans-serif;font-weight:500;font-size:22px;color:var(--white)}
.field{left:693px;width:392px;height:47px;background:rgba(255,255,255,.16);border-radius:3px;color:var(--white);font-size:13px;font-weight:700;display:flex;align-items:center;padding-left:52px}
.submit{left:693px;top:328px;width:392px;height:45px;background:var(--orange);color:var(--white);font-weight:900;font-size:15px;border-radius:3px;display:flex;align-items:center;justify-content:center}

/* reviews */
.reviews{top:3059px;height:693px;background:var(--white)}
.reviews-eyebrow{left:0;width:1200px;text-align:center;top:89px}
.reviews-title{left:0;width:1200px;text-align:center;top:118px;font-size:48px}
.review{top:0;width:340px;height:520px}
.review-photo{left:0;top:227px;width:87px;height:120px;background:linear-gradient(180deg,#cfd3da,#8e97a6 60%,#3f4658)}
.review-name{left:113px;top:247px;font-family:"Ubuntu",sans-serif;font-weight:500;font-size:18px;color:var(--ink)}
.review-role{left:113px;top:276px;font-size:13px}
.review-card{left:21px;top:335px;width:302px;height:176px;background:var(--white);box-shadow:0 3px 14px rgba(0,0,0,.1);padding:36px 18px 0 34px;font-size:14.5px;line-height:24.6px}
.review-quote{left:266px;top:296px;font-family:"Ubuntu",sans-serif;font-weight:700;font-size:64px;line-height:1;height:40px;color:var(--orange);z-index:2}
.reviews-btn{left:521px;top:569px;width:154px;height:44px}

/* footer */
.site-footer{top:3752px;height:425px;background:var(--navy-deep);color:var(--white)}
.footer-brand{left:120px;top:114px;font-family:"Ubuntu",sans-serif;font-weight:500;font-size:52px;color:var(--orange);line-height:1}
.footer-note{left:114px;top:185px;width:220px;font-size:13px;font-weight:700;line-height:25px}
.social{top:284px;width:29px;height:29px;border:1px solid rgba(255,255,255,.35);border-radius:3px;background:rgba(255,255,255,.06)}
.footer-heading{top:109px;font-family:"Ubuntu",sans-serif;font-weight:500;font-size:19px}
.footer-small{left:517px;top:155px;width:210px;font-size:12px;font-weight:700;line-height:25px}
.newsletter-input{left:517px;top:246px;width:223px;height:41px;background:rgba(255,255,255,.14);border-radius:3px;font-size:12px;font-weight:700;display:flex;align-items:center;justify-content:space-between;padding:0 14px}
.contact-row{left:860px;display:flex;gap:16px;align-items:flex-start}
.contact-row b{display:block;font-family:"Ubuntu",sans-serif;font-weight:500;font-size:16px}
.contact-row span{display:block;font-size:14px;margin-top:6px;font-weight:700}
.copyright{left:514px;top:396px;font-size:14px;font-weight:700}
.to-top{left:1062px;top:387px;width:34px;height:34px;background:var(--orange);display:flex;align-items:center;justify-content:center}
</style>
</head>
<body>

<header class="site-header abs" style="left:0;width:1200px">
  <div class="topbar abs">
    <div class="topbar-item abs" style="left:63px">
      <svg width="14" height="14" viewBox="0 0 24 24" fill="none" stroke="#fff" stroke-width="2"><path d="M5 3h4l2 5-3 2a12 12 0 0 0 6 6l2-3 5 2v4a2 2 0 0 1-2 2A18 18 0 0 1 3 5a2 2 0 0 1 2-2z"/></svg>
      555 - 010 - 4821
    </div>
    <div class="topbar-item topbar-cta abs">
      <svg width="16" height="12" viewBox="0 0 24 18" fill="none" stroke="#fff" stroke-width="2"><rect x="1" y="1" width="22" height="16" rx="2"/><path d="M1 2l11 8 11-8"/></svg>
      REQUEST AN APPOINTMENT
    </div>
    <div class="topbar-item abs" style="left:477px">
      <svg width="12" height="14" viewBox="0 0 20 24" fill="none" stroke="#fff" stroke-width="2"><path d="M10 23s8-8 8-13a8 8 0 0 0-16 0c0 5 8 13 8 13z"/><circle cx="10" cy="10" r="3"/></svg>
      12 Sample Lane Anywhere
    </div>
  </div>
  <div class="brand abs">lernwandel</div>
  <nav class="nav">
    <a class="active" style="left:397px">Home</a>
    <a style="left:472px">About Us</a>
    <a style="left:547px">Services</a>
    <a style="left:621px">Apprentices</a>
    <a style="left:709px">Host families</a>
    <a style="left:798px">Companies</a>
  </nav>
  <div class="header-cta abs">CONTACT US</div>
</header>

<section class="hero">
  <div class="hero-photo abs" role="img" aria-label="Smiling colleagues shaking hands in a bright office"></div>
  <div class="hero-shade abs"></div>
  <div class="hero-badge abs">WELCOME</div>
  <h1 class="hero-title abs">Bridging Skills for<br>the future</h1>
  <div class="hero-btn abs">ABOUT COMPANY</div>
</section>

<section class="about">
  <svg class="mosaic abs" width="520" height="520" viewBox="0 0 520 520" role="img" aria-label="Diamond collage of apprentices: a chef, workshop trainees, a mechanic and kitchen staff">
    <defs>
      <linearGradient id="q1" x1="0" y1="0" x2="1" y2="1"><stop offset="0" stop-color="#3b3130"/><stop offset="1" stop-color="#c9b6a8"/></linearGradient>
      <linearGradient id="q2" x1="0" y1="0" x2="1" y2="1"><stop offset="0" stop-color="#1f2c55"/><stop offset="1" stop-color="#6b7a9a"/></linearGradient>
      <linearGradient id="q3" x1="0" y1="0" x2="1" y2="1"><stop offset="0" stop-color="#5a6b88"/><stop offset="1" stop-color="#1c2846"/></linearGradient>
      <linearGradient id="q4" x1="0" y1="0" x2="1" y2="1"><stop offset="0" stop-color="#bdbdbd"/><stop offset="1" stop-color="#3e3a38"/></linearGradient>
    </defs>
    <g stroke="#fff" stroke-width="8" stroke-linejoin="miter">
      <polygon points="260,10 385,135 260,260 135,135" fill="url(#q1)"/>
      <polygon points="135,135 260,260 135,385 10,260" fill="url(#q2)"/>
      <polygon points="385,135 510,260 385,385 260,260" fill="url(#q3)"/>
      <polygon points="260,260 385,385 260,510 135,385" fill="url(#q4)"/>
    </g>
    <circle cx="260" cy="260" r="48" fill="#fff"/>
  </svg>
  <div class="about-eyebrow eyebrow abs">What We Do</div>
  <h2 class="about-title heading abs">Skills Shared, Success Multiplied</h2>
  <p class="about-text abs">Lorem ipsum dolor sit amet, consectetur adipiscing elit, sed do eiusmod tempor incididunt ut labore et dolore magna aliqua. Ut enim ad minim veniam, quis nostrud exercitation ullamco laboris nisi ut aliquip ex ea commodo consequat. Duis aute irure dolor in reprehenderit in voluptate velit esse cillum dolore eu fugiat nulla pariatur. Excepteur sint occaecat cupidatat non proident, sunt in culpa qui officia deserunt mollit. ehenderit in voluptate velit esse cillum dolore eu fugiat nulla pariatur. Excepteur sint occaecat cupidatat non proident, sunt in culpa qui officia.</p>
  <div class="about-btn btn-orange abs">Contact us
    <svg width="18" height="14" viewBox="0 0 18 14" fill="none" stroke="#fff" stroke-width="2"><path d="M1 7h15M10 1l6 6-6 6"/></svg>
  </div>
</section>

<section class="services">
  <div class="services-eyebrow eyebrow abs">What We Do</div>
  <h2 class="services-title heading abs">Services That We Provide</h2>

  <div class="service-card abs" style="left:94px">
    <div class="service-photo abs" role="img" aria-label="Young team smiling around a meeting table" style="background:linear-gradient(135deg,#c9b089,#7e6a55 50%,#3b3a3c)"></div>
    <div class="service-ring abs"></div>
    <div class="service-icon abs"><svg width="30" height="30" viewBox="0 0 24 24" fill="none" stroke="#fff" stroke-width="1.6"><path d="M12 3l2.5 5 5.5.8-4 3.9.9 5.5L12 15.6 7.1 18.2 8 12.7 4 8.8 9.5 8z"/></svg></div>
    <div class="service-label abs"><h3>Apprentice Matching</h3><p>Read More &nbsp;›</p></div>
  </div>

  <div class="service-card abs" style="left:441px">
    <div class="service-photo abs" role="img" aria-label="Colleagues gathered around a laptop" style="background:linear-gradient(135deg,#9fae8a,#6a6e55 45%,#2d3230)"></div>
    <div class="service-ring abs"></div>
    <div class="service-icon abs"><svg width="30" height="30" viewBox="0 0 24 24" fill="none" stroke="#fff" stroke-width="1.6"><path d="M4 17a8 8 0 1 1 16 0"/><path d="M12 17l4-5"/><circle cx="12" cy="17" r="1.2"/></svg></div>
    <div class="service-label abs"><h3>Industry Networking</h3><p>Read More &nbsp;›</p></div>
  </div>

  <div class="service-card abs" style="left:785px">
    <div class="service-photo abs" role="img" aria-label="Mentor guiding trainees at computer workstations" style="background:linear-gradient(135deg,#b4bfcf,#6d7a92 45%,#2c3447)"></div>
    <div class="service-ring abs"></div>
    <div class="service-icon abs"><svg width="30" height="30" viewBox="0 0 24 24" fill="none" stroke="#fff" stroke-width="1.6"><circle cx="12" cy="6" r="2.5"/><path d="M12 9l-4 9h8z"/><path d="M5 20h14"/></svg></div>
    <div class="service-label abs"><h3>Career Guidance</h3><p>Read More &nbsp;›</p></div>
  </div>
</section>

<section class="projects">
  <h2 class="projects-title heading abs">Ready to bring bigger and<br>stronger projects than before</h2>
  <div class="tab active abs" style="left:107px;width:161px">For Apprentices</div>
  <div class="tab abs" style="left:282px;width:161px">For Host families</div>
  <div class="tab abs" style="left:464px;width:149px">For Companies</div>
  <div class="projects-photo abs" role="img" aria-label="Two young men working together on a laptop"></div>
  <p class="projects-text abs">Lorem ipsum dolor sit amet, consectetur eiusmod tempor incididunt ut labore et dolore im ad minim veniam, quis nostrud exercitation eiusmod tempor incididunt ut labore et dolore im ad minim veniam, quis nostrud exercitation</p>
  <div class="check abs" style="top:425px"><svg width="16" height="16" viewBox="0 0 16 16" fill="none" stroke="#ff7a00" stroke-width="1.5"><rect x="1" y="2" width="12" height="12"/><path d="M4 8l3 3 7-8"/></svg>Award winning company</div>
  <div class="check abs" style="top:459px"><svg width="16" height="16" viewBox="0 0 16 16" fill="none" stroke="#ff7a00" stroke-width="1.5"><rect x="1" y="2" width="12" height="12"/><path d="M4 8l3 3 7-8"/></svg>Award winning company</div>
  <div class="check abs" style="top:493px"><svg width="16" height="16" viewBox="0 0 16 16" fill="none" stroke="#ff7a00" stroke-width="1.5"><rect x="1" y="2" width="12" height="12"/><path d="M4 8l3 3 7-8"/></svg>Award winning company</div>
  <div class="projects-people abs" role="img" aria-label="Senior mentor and young woman reviewing a tablet together"></div>
</section>

<section class="enroll">
  <div class="enroll-bg abs" role="img" aria-label="Team discussion in a modern office, muted in blue"></div>
  <div class="enroll-shade abs"></div>
  <h2 class="enroll-title heading abs">Empowering Careers,<br>One Exchange Program<br>at a Time</h2>
  <div class="enroll-form-title abs">Enroll For Program</div>
  <div class="field abs" style="top:130px">Full Name</div>
  <div class="field abs" style="top:196px">Email Address</div>
  <div class="field abs" style="top:261px">Industry</div>
  <div class="submit abs">SUBMIT</div>
</section>

<section class="reviews">
  <div class="reviews-eyebrow eyebrow abs">Testimonials</div>
  <h2 class="reviews-title heading abs">Clients Reviews</h2>

  <div class="review abs" style="left:91px">
    <div class="review-photo abs" role="img" aria-label="Portrait of an apprentice"></div>
    <div class="review-name abs">Jonas Berger</div>
    <div class="review-role abs">Apprentice</div>
    <div class="review-card abs">Lorem ipsum dolor sit amet, consect etur adipiscing elit, sed do eiusmod tempor incididunt ut labore et dolore magna aliqua. Ut enim ad minim veni am, quis nostrud</div>
    <div class="review-quote abs">“</div>
  </div>

  <div class="review abs" style="left:438px">
    <div class="review-photo abs" role="img" aria-label="Portrait of a host family member"></div>
    <div class="review-name abs">Lea Marchetti</div>
    <div class="review-role abs">Host Family</div>
    <div class="review-card abs">Lorem ipsum dolor sit amet, consect etur adipiscing elit, sed do eiusmod tempor incididunt ut labore et dolore magna aliqua. Ut enim ad minim veni am, quis nostrud</div>
    <div class="review-quote abs">“</div>
  </div>

  <div class="review abs" style="left:787px">
    <div class="review-photo abs" role="img" aria-label="Portrait of a company representative"></div>
    <div class="review-name abs">Elias Brunner</div>
    <div class="review-role abs">Company</div>
    <div class="review-card abs">Lorem ipsum dolor sit amet, consect etur adipiscing elit, sed do eiusmod tempor incididunt ut labore et dolore magna aliqua. Ut enim ad minim veni am, quis nostrud</div>
    <div class="review-quote abs">“</div>
  </div>

  <div class="reviews-btn btn-orange abs">Contact us
    <svg width="18" height="14" viewBox="0 0 18 14" fill="none" stroke="#fff" stroke-width="2"><path d="M1 7h15M10 1l6 6-6 6"/></svg>
  </div>
</section>

<footer class="site-footer abs" style="left:0;width:1200px">
  <div class="footer-brand abs">lernwandel</div>
  <p class="footer-note abs">Subscribe to our newsletter to recieve updates or the latest news</p>
  <div class="social abs" style="left:114px" aria-label="Social link"></div>
  <div class="social abs" style="left:156px" aria-label="Social link"></div>
  <div class="social abs" style="left:196px" aria-label="Social link"></div>
  <div class="social abs" style="left:238px" aria-label="Social link"></div>

  <div class="footer-heading abs" style="left:517px">Newsletter</div>
  <p class="footer-small abs">Subscribe to our newsletter to recieve updates or the latest news</p>
  <div class="newsletter-input abs">Subscribe with us
    <svg width="10" height="14" viewBox="0 0 10 14" fill="none" stroke="#fff" stroke-width="2"><path d="M2 1l6 6-6 6"/></svg>
  </div>

  <div class="footer-heading abs" style="left:860px">Contacts</div>
  <div class="contact-row abs" style="top:160px">
    <svg width="32" height="34" viewBox="0 0 32 34" fill="none" stroke="#ff7a00" stroke-width="1.6"><rect x="3" y="2" width="16" height="30" rx="3"/><path d="M9 27h4"/><path d="M23 11a6 6 0 0 1 0 10M26 8a10 10 0 0 1 0 16"/></svg>
    <div><b>Contact Us</b><span>(44) 555-010-789</span></div>
  </div>
  <div class="contact-row abs" style="top:231px">
    <svg width="32" height="34" viewBox="0 0 32 34" fill="none" stroke="#ff7a00" stroke-width="1.6"><path d="M2 14l14-11 14 11v18H2z"/><path d="M2 14l14 10 14-10"/><path d="M8 11h16M8 15h16"/></svg>
    <div><b>Contact Us</b><span>(44) 555-010-789</span></div>
  </div>

  <div class="copyright abs">Lernwandel Apprentices Exchange</div>
  <div class="to-top abs"><svg width="16" height="10" viewBox="0 0 16 10" fill="none" stroke="#fff" stroke-width="2.2"><path d="M1 9l7-7 7 7"/></svg></div>
</footer>

</body>
</html>
```